Los Angeles based Demolition, Grading, and Structural concrete Contractor in need of a Sale brochure

We are a Los Angeles-based demolition, grading, and structural concrete contractor looking for a professionally designed sales brochure that represents our company and services. The brochure should be visually appealing, easy to read, and include the following:

-Company Logo: Prominently displayed to enhance brand identity.

-Services We Offer: A clear breakdown of our key services, including demolition, grading, and structural concrete work.

-Project Scope & Capabilities: A brief explanation of the type of projects we handle (residential, commercial, industrial).

-Pricing Information: Mention that demolition services start at $20,000. This price includes complete demolition of structure, safe debris removal and hauling, site preparation for new construction.

-Contact Information: Our phone number(818.502.6617), email(contact@brovanbuildersinc.example) , and website for potential clients to reach out.

The design should reflect the professionalism and strength of our industry, using a modern, clean layout with bold colors that align with construction and demolition themes. Images of past work or stock photos representing our services are encouraged.

Final deliverables should be print-ready (PDF) and digital-friendly formats. Looking forward to creative and impactful designs!

```html
<!DOCTYPE html>
<html lang="en">
<head>
<meta charset="UTF-8">
<title>Brovan Builders – Sales Flyer</title>
<link href="https://fonts.googleapis.com/css2?family=Inter:wght@400;500;600;700;800&display=swap" rel="stylesheet">
<style>
  :root {
    --brand-blue: #1b75bc;
    --brand-blue-dark: #155f9a;
    --panel-tint: #e3ecf5;
    --ink: #1d1d1f;
    --muted: #6d6e71;
    --paper: #ffffff;
    --backdrop: #d4d4d4;
  }
  * { margin: 0; padding: 0; box-sizing: border-box; }
  html, body { width: 714px; height: 1200px; overflow: hidden; }
  body {
    background: var(--backdrop);
    font-family: "Inter", Arial, sans-serif;
    color: var(--ink);
    position: relative;
  }
  .flyer {
    position: absolute;
    left: 0; top: 132px;
    width: 714px; height: 935px;
    background: var(--paper);
    overflow: hidden;
    box-shadow: 0 2px 8px rgba(0,0,0,.25);
  }
  .abs { position: absolute; }

  /* header */
  .brand-block {
    left: 42px; top: 0; width: 201px; height: 134px;
    background: var(--brand-blue);
    display: flex; flex-direction: column; justify-content: center; align-items: center;
    color: #fff; font-weight: 800; font-size: 27px; line-height: 1.15; letter-spacing: 1px;
    text-align: center;
  }
  .headline {
    left: 267px; top: 18px;
    font-size: 36px; font-weight: 800; line-height: 37px;
    color: var(--brand-blue); letter-spacing: -0.5px;
  }
  .service-line {
    left: 270px; top: 103px;
    font-size: 15px; font-weight: 600; color: var(--muted);
  }
  .service-line span { margin: 0 5px; color: var(--brand-blue); }

  /* photos */
  .photo { background: linear-gradient(160deg, #8e9aa0 0%, #b59a72 55%, #d2b98f 100%); }
  .hero-photo { left: 0; top: 148px; width: 714px; height: 285px;
    background: linear-gradient(180deg, #7f8a8c 0%, #9aa0a0 35%, #c3a77e 65%, #d9c19a 100%); }

  /* services panel */
  .services-head {
    left: 361px; top: 219px; width: 311px; height: 62px;
    background: var(--brand-blue); color: #fff;
    font-size: 31px; font-weight: 800; display: flex; align-items: center; justify-content: center;
  }
  .services-panel { left: 363px; top: 281px; width: 309px; height: 637px; background: var(--panel-tint); }
  .service-img { left: 380px; width: 272px; height: 129px; }
  .service-title { left: 380px; font-size: 21px; font-weight: 700; }
  .service-text { left: 380px; width: 275px; font-size: 12px; line-height: 14px; color: #333; }

  /* left column */
  .section-title { left: 43px; font-size: 21px; font-weight: 800; line-height: 26px; }
  .rule { left: 43px; width: 95px; height: 3px; background: var(--brand-blue); }
  .price-lead { left: 42px; top: 517px; font-size: 16px; font-weight: 700; }
  .checklist { left: 44px; top: 545px; list-style: none; font-size: 14px; font-weight: 500; }
  .checklist li { display: flex; align-items: center; height: 23px; }
  .checklist svg { width: 17px; height: 14px; margin-right: 9px; }
  .scope-text { left: 38px; top: 721px; width: 318px; font-size: 11.6px; line-height: 16.5px; color: #333; }

  /* footer */
  .footer-band { left: 0; top: 813px; width: 714px; height: 122px; background: var(--brand-blue); }
  .call-label { left: 42px; top: 828px; font-size: 20px; font-weight: 600; color: #fff; }
  .call-number { left: 42px; top: 852px; font-size: 23px; font-weight: 500; color: #fff; letter-spacing: .3px; }
  .contact-line { left: 42px; font-size: 12.5px; color: #fff; display: flex; align-items: center; }
  .contact-line svg { width: 10px; height: 10px; margin-right: 9px; }
</style>
</head>
<body>
<main class="flyer">
  <div class="abs brand-block"><span>BROVAN</span><span>BUILDERS</span></div>
  <h1 class="abs headline">Built for Strength,<br>Engineered for Success</h1>
  <p class="abs service-line">DEMOLITION<span>•</span>GRADING<span>•</span>STRUCTURAL CONCRETE</p>

  <div class="abs photo hero-photo" role="img" aria-label="Red compact excavator working on a graded site in front of a concrete retaining wall"></div>

  <div class="abs services-panel"></div>
  <h2 class="abs services-head">OUR SERVICES</h2>

  <div class="abs photo service-img" style="top:305px" role="img" aria-label="Yellow excavator demolishing a structure among trees"></div>
  <h3 class="abs service-title" style="top:449px">Demolition</h3>
  <p class="abs service-text" style="top:473px">Safe, efficient, and complete structure removal, including debris hauling.</p>

  <div class="abs photo service-img" style="top:512px" role="img" aria-label="Graded site beside a long concrete retaining wall"></div>
  <h3 class="abs service-title" style="top:655px">Grading</h3>
  <p class="abs service-text" style="top:679px">Site preparation for new builds, leveling, excavation, and soil stabilization.</p>

  <div class="abs photo service-img" style="top:718px" role="img" aria-label="Aerial view of a structural concrete foundation under construction"></div>
  <h3 class="abs service-title" style="top:861px">Structural Concrete</h3>
  <p class="abs service-text" style="top:885px">Foundations, retaining walls, slabs, and reinforced concrete work.</p>

  <h2 class="abs section-title" style="top:459px">TRANSPARENT PRICING</h2>
  <div class="abs rule" style="top:493px"></div>
  <p class="abs price-lead">Demolition services start at $20,000</p>
  <ul class="abs checklist">
    <li><svg viewBox="0 0 17 14"><path d="M1.5 7.5l4.5 4.5L15.5 2" fill="none" stroke="#1b75bc" stroke-width="3"/></svg>Complete structure removal</li>
    <li><svg viewBox="0 0 17 14"><path d="M1.5 7.5l4.5 4.5L15.5 2" fill="none" stroke="#1b75bc" stroke-width="3"/></svg>Safe debris removal &amp; hauling</li>
    <li><svg viewBox="0 0 17 14"><path d="M1.5 7.5l4.5 4.5L15.5 2" fill="none" stroke="#1b75bc" stroke-width="3"/></svg>Site preparation for new construction</li>
  </ul>

  <h2 class="abs section-title" style="top:634px;left:38px">PROJECT SCOPE &amp;<br>CAPABILITIES</h2>
  <div class="abs rule" style="top:698px;left:38px"></div>
  <p class="abs scope-text">We handle projects of all sizes, from small-scale residential demolitions to large commercial and industrial site preparations. Our skilled team ensures compliance with local regulations and industry best practices, delivering quality work on time and within budget.</p>

  <div class="abs footer-band"></div>
  <div class="abs services-panel" style="top:813px;height:105px"></div>
  <div class="abs photo service-img" style="top:718px" role="img" aria-label="Aerial view of a structural concrete foundation under construction"></div>
  <h3 class="abs service-title" style="top:861px">Structural Concrete</h3>
  <p class="abs service-text" style="top:885px">Foundations, retaining walls, slabs, and reinforced concrete work.</p>

  <p class="abs call-label">Call Us</p>
  <p class="abs call-number">818.502.6617</p>
  <p class="abs contact-line" style="top:886px"><svg viewBox="0 0 10 10"><rect x="0.5" y="1.5" width="9" height="7" fill="none" stroke="#fff"/><path d="M0.5 1.5l4.5 4 4.5-4" fill="none" stroke="#fff"/></svg>contact@brovanbuildersinc.example</p>
  <p class="abs contact-line" style="top:905px"><svg viewBox="0 0 10 10"><circle cx="5" cy="5" r="4.5" fill="none" stroke="#fff"/><path d="M0.5 5h9M5 0.5c-2.5 2.5-2.5 6.5 0 9M5 0.5c2.5 2.5 2.5 6.5 0 9" fill="none" stroke="#fff" stroke-width=".8"/></svg>www.brovanbuildersinc.example</p>
</main>
</body>
</html>
```